Web portal for events

The project is about creating a web application - portal for culture events in Denmark.

Design

We aim for very simplistic, light and fully responsive design. The white background is preferable, as well as light color tones. As inspirational points we like the colors used in www.parvolio.com and www.brindlemoor.org

FORMAT AND REQUIREMENTS:
1. Design should be provided based on the wireframes specified as a link below.
2. The design (and all of its pages) should be provided in three resolution variants:
- Desktop
- Tablet
- Phone
3. The design should be provided as PSD, where each page/section should be in its own PSD file
4. All graphical elements in the design should be delivered as single layers which can then be extracted from the PSD.
5. All graphical elements (icons, graphical buttons, etc.) should be provided as vector objects in the PSD, so that they can be exported into different sizes without loss of quality (for responsiveness)
6. The design should use either web safe fonts or Google Fonts.

RESPONSIVENESS
The web application should be visible on any devices (i.e. responsive design)

WIREFRAMES:
https://velkotrams.examplewire.com/projects/fennoplex/prototype/Homepage?key=3b7c19d0f2a84e6c5d1e9a07b4f2c8d6e1a3f590

We expect design of the following wireframes:

Homepage:
https://velkotrams.examplewire.com/projects/fennoplex/Homepage

For arrangører - billede uploaded:
https://velkotrams.examplewire.com/projects/fennoplex/For%20arrang%C3%B8rer%20-%20billede%20uploaded

Further specifications of the project (i.e. functionality, etc.):
https://files.quorvane.net/document/d/8pKw_Rt2mZqLx4NvB7yHc0aEs9uGdJf3TiOb6nVlW1k/edit?usp=sharing

```html
<!DOCTYPE html>
<html lang="da">
<head>
<meta charset="utf-8">
<title>KULTIVA – Din guide til kultur og events</title>
<link rel="stylesheet" href="https://fonts.googleapis.com/css2?family=Roboto:ital,wght@0,400;0,500;0,700;0,900;1,400&display=swap">
<style>
:root{
  --red:#f2421b;
  --red-text:#e8401c;
  --dark:#3d3d3d;
  --slate:#5a6370;
  --grey-bg:#ececec;
  --footer:#4a4a4a;
  --text:#7b7b7b;
  --line:#d4d4d4;
  --star:#e6b93a;
  --star-off:#bdbdbd;
}
*{box-sizing:border-box;margin:0;padding:0}
html,body{width:757px;height:1200px;overflow:hidden;background:#fff}
body{font-family:"Roboto",Arial,sans-serif;color:var(--text)}
.page{position:relative;width:946px;height:1500px;transform:scale(.8);transform-origin:0 0}
.abs{position:absolute}

/* header */
.brand{left:135px;top:14px}
.brand-name{font-size:23px;font-weight:900;color:#6a6a6a;letter-spacing:1px}
.brand-tag{font-size:8px;color:#888;margin-top:2px}
.search{left:288px;top:22px;width:275px;height:26px;border:1px solid var(--line);border-radius:3px;display:flex;align-items:center;font-size:8px;color:#888}
.search svg{margin:0 10px 0 10px}
.search span{border-left:1px solid var(--line);padding-left:10px;height:100%;display:flex;align-items:center}
.btn-dark{background:var(--slate);color:#fff;border-radius:3px;font-size:8px;display:flex;align-items:center;justify-content:center}
.go{left:573px;top:22px;width:28px;height:26px}
.adv{left:607px;top:22px;width:96px;height:26px}
.login{left:709px;top:22px;width:102px;height:26px;border:1px solid var(--line);border-radius:3px;background:#f4f4f4;font-size:8px;color:#777;display:flex;align-items:center;justify-content:center;gap:6px}

/* nav */
.nav{left:0;top:67px;width:946px;height:30px;background:var(--red)}
.nav ul{list-style:none;position:absolute;left:137px;top:0;display:flex;height:30px}
.nav li{color:#fff;font-size:8.5px;font-weight:500;display:flex;align-items:center;justify-content:center;border-right:1px solid rgba(0,0,0,.15)}
.nav li.on{background:var(--dark)}

/* hero */
.hero{left:0;top:97px;width:946px;height:325px;background:linear-gradient(100deg,#5c6a78 0%,#2b2622 22%,#3a2519 40%,#a4714f 62%,#e3c0a4 78%,#6d4a36 100%)}
.hero-shade{left:0;top:97px;width:946px;height:325px;background:linear-gradient(90deg,rgba(0,0,0,.35),rgba(0,0,0,0) 60%)}
.hero-title{left:141px;top:264px;font-size:37px;font-weight:900;color:#fff}
.hero-sub{left:141px;top:313px;font-size:20px;font-weight:900;color:#fff;line-height:29px}
.arrow{top:225px}

/* sort bar */
.section-label{font-size:8.5px;font-weight:500;color:var(--red-text)}
.sort-label{left:243px;top:459px;font-size:8px;color:#666}
.sort-on{left:290px;top:452px;width:71px;height:22px}
.select{top:452px;height:22px;border:1px solid #c9c9c9;border-radius:2px;font-size:8px;color:#666;display:flex;align-items:center;padding-left:10px}
.select i{position:absolute;right:4px;top:6px;width:9px;height:9px;border:1px solid #888;font-style:normal}
.select i::after{content:"";position:absolute;left:2px;top:3px;border:2px solid transparent;border-top:3px solid #555}

/* cards */
.card{width:139px;height:200px}
.photo{position:absolute;left:0;top:0;width:139px;height:93px}
.card h3{position:absolute;top:104px;font-size:8px;font-weight:500;color:var(--red-text)}
.card p{position:absolute;top:120px;font-size:7.5px;line-height:15px;width:150px}
.meta{position:absolute;top:155px;left:0;width:139px;font-size:6.8px;font-style:italic;color:#555;display:flex;justify-content:space-between}
.stars{font-style:normal;font-size:8px;letter-spacing:-.5px;color:var(--star)}
.stars b{color:var(--star-off);font-weight:400}
.pill{position:absolute;top:176px;height:19px;border:1px solid #c6c6c6;border-radius:2px;background:linear-gradient(#fafafa,#e8e8e8);font-size:7.5px;color:var(--red-text);display:flex;align-items:center;justify-content:center}

/* pagination */
.pager{left:280px;top:1372px;display:flex;gap:8px}
.pager span{height:19px;min-width:19px;border:1px solid #ccc;border-radius:2px;font-size:8px;font-weight:500;color:#555;display:flex;align-items:center;justify-content:center;padding:0 4px}
.pager .wide{width:39px}

/* sidebar */
.sidebar{left:608px;top:446px;width:203px;height:944px;background:var(--grey-bg)}
.fav{left:629px;width:160px;height:100px}
.fav .cap{position:absolute;left:0;bottom:0;width:100%;height:22px;background:rgba(0,0,0,.55);color:#fff;font-size:7.5px;font-weight:500;padding:8px 0 0 11px}
.sidebar-btn{left:629px;width:129px;height:24px}
.news-text{left:629px;top:908px;width:160px;font-size:7.5px;line-height:15px}
.email{left:629px;top:960px;width:160px;height:24px;background:#fff;border:1px solid #d0d0d0;border-radius:2px;font-size:7.5px;color:#777;padding:7px 11px}

/* footer */
.footer{left:0;top:1426px;width:946px;height:74px;background:var(--footer)}
.foot-links{left:136px;top:1448px;display:flex;font-size:7px;color:#c8c8c8}
.foot-links span{margin-right:0}
.copy{left:136px;top:1471px;font-size:7px;color:#c8c8c8}
.social{top:1453px;width:22px;height:22px;border-radius:50%;background:#8a8a8a}
</style>
</head>
<body>
<div class="page">

  <header>
    <div class="abs brand">
      <div class="brand-name">KULTIVA</div>
      <div class="brand-tag">Din guide til Kultur og events</div>
    </div>
    <div class="abs search">
      <svg width="12" height="12" viewBox="0 0 12 12"><circle cx="5" cy="5" r="3.8" fill="none" stroke="#999" stroke-width="1.3"/><line x1="8" y1="8" x2="11" y2="11" stroke="#999" stroke-width="1.5"/></svg>
      <span>Search</span>
    </div>
    <div class="abs btn-dark go">GO</div>
    <div class="abs btn-dark adv">avanceret søgning</div>
    <div class="abs login">
      <svg width="12" height="12" viewBox="0 0 12 12"><circle cx="6" cy="6" r="4.2" fill="none" stroke="#888" stroke-width="2.4" stroke-dasharray="2 1.3"/><circle cx="6" cy="6" r="2" fill="#888"/></svg>
      Login / Signup
    </div>
  </header>

  <nav class="abs nav">
    <ul>
      <li class="on" style="width:67px">ALLE</li>
      <li style="width:63px">MUSIK</li>
      <li style="width:72px">SPORT</li>
      <li style="width:72px">TEATER</li>
      <li style="width:92px">UDSTILLING</li>
      <li style="width:73px">FELDRE</li>
      <li style="width:66px">BORN</li>
      <li style="width:74px">MOTION</li>
      <li style="width:79px">DIVERSE</li>
    </ul>
  </nav>

  <section>
    <div class="abs hero" role="img" aria-label="Photo of friends toasting with glasses of red wine"></div>
    <div class="abs hero-shade"></div>
    <svg class="abs arrow" style="left:60px" width="14" height="50" viewBox="0 0 14 50"><polyline points="12,2 2,25 12,48" fill="none" stroke="rgba(255,255,255,.35)" stroke-width="1.5"/></svg>
    <svg class="abs arrow" style="left:878px" width="14" height="50" viewBox="0 0 14 50"><polyline points="2,2 12,25 2,48" fill="none" stroke="rgba(255,255,255,.35)" stroke-width="1.5"/></svg>
    <div class="abs hero-title">KULTIVA</div>
    <div class="abs hero-sub">FEATURING POPULAR<br>CULTURAL EVENTS IN DENMARK</div>
  </section>

  <main>
    <div class="abs section-label" style="left:135px;top:459px">POPULARE EVENTS</div>
    <div class="abs sort-label">Sorter efter</div>
    <div class="abs btn-dark sort-on">Populare</div>
    <div class="abs select" style="left:370px;width:70px">Omrade<i></i></div>
    <div class="abs select" style="left:446px;width:57px">Date<i></i></div>
    <div class="abs select" style="left:509px;width:57px">Time<i></i></div>

    <!-- row 1 -->
    <article class="abs card" style="left:135px;top:501px"><div class="photo" role="img" aria-label="Photo of guests dining at a restaurant table" style="background:linear-gradient(135deg,#3a2a22,#8a6a55 50%,#2a201c)"></div><h3>JONAS KRELL KONCERT</h3><p>Lorem Ipsum is simply dummy text of the printing...</p><div class="meta">Posted on 20 Feb 2014<span class="stars">★★★<b>★★</b></span></div><div class="pill" style="left:0;width:51px">Event</div><div class="pill" style="left:57px;width:82px">Till mine favorite</div></article>
    <article class="abs card" style="left:291px;top:501px"><div class="photo" role="img" aria-label="Photo of a plated grilled meat dish" style="background:linear-gradient(135deg,#e8e2da,#8c5a34 55%,#f1ece5)"></div><h3>JONAS KRELL KONCERT</h3><p>Lorem Ipsum is simply dummy text of the printing...</p><div class="meta">Posted on 20 Feb 2014<span class="stars">★★★<b>★★</b></span></div><div class="pill" style="left:0;width:51px">Event</div><div class="pill" style="left:57px;width:82px">Till mine favorite</div></article>
    <article class="abs card" style="left:447px;top:501px"><div class="photo" role="img" aria-label="Photo of a gourmet plate with wine glasses" style="background:linear-gradient(160deg,#3b2414,#a5652c 55%,#e8d8c8)"></div><h3>JONAS KRELL KONCERT</h3><p>Lorem Ipsum is simply dummy text of the printing...</p><div class="meta">Posted on 20 Feb 2014<span class="stars">★★★<b>★★</b></span></div><div class="pill" style="left:0;width:51px">Event</div><div class="pill" style="left:57px;width:82px">Till mine favorite</div></article>

    <!-- row 2 -->
    <article class="abs card" style="left:135px;top:717px"><div class="photo" role="img" aria-label="Photo of a concert crowd under stage lights" style="background:linear-gradient(160deg,#d07a22,#5a2410 50%,#120806)"></div><h3>JONAS KRELL KONCERT</h3><p>Lorem Ipsum is simply dummy text of the printing...</p><div class="meta">Posted on 20 Feb 2014<span class="stars">★★★<b>★★</b></span></div><div class="pill" style="left:0;width:51px">Event</div><div class="pill" style="left:57px;width:82px">Till mine favorite</div></article>
    <article class="abs card" style="left:291px;top:717px"><div class="photo" role="img" aria-label="Photo of couples dining together" style="background:linear-gradient(135deg,#4a3a30,#b08a6a 50%,#3a2a24)"></div><h3>JONAS KRELL KONCERT</h3><p>Lorem Ipsum is simply dummy text of the printing...</p><div class="meta">Posted on 20 Feb 2014<span class="stars">★★★<b>★★</b></span></div><div class="pill" style="left:0;width:51px">Event</div><div class="pill" style="left:57px;width:82px">Till mine favorite</div></article>
    <article class="abs card" style="left:447px;top:717px"><div class="photo" role="img" aria-label="Photo of a candlelit dinner table with red wine" style="background:linear-gradient(150deg,#2a160a,#8a4a1e 50%,#d9b89a)"></div><h3>JONAS KRELL KONCERT</h3><p>Lorem Ipsum is simply dummy text of the printing...</p><div class="meta">Posted on 20 Feb 2014<span class="stars">★★★<b>★★</b></span></div><div class="pill" style="left:0;width:51px">Event</div><div class="pill" style="left:57px;width:82px">Till mine favorite</div></article>

    <!-- row 3 -->
    <article class="abs card" style="left:135px;top:934px"><div class="photo" role="img" aria-label="Photo of champagne glasses in a lit venue" style="background:linear-gradient(135deg,#2a3a7a,#a0502a 50%,#3a1a1a)"></div><h3>JONAS KRELL KONCERT</h3><p>Lorem Ipsum is simply dummy text of the printing...</p><div class="meta">Posted on 20 Feb 2014<span class="stars">★★★<b>★★</b></span></div><div class="pill" style="left:0;width:51px">Event</div><div class="pill" style="left:57px;width:82px">Till mine favorite</div></article>
    <article class="abs card" style="left:291px;top:934px"><div class="photo" role="img" aria-label="Photo of a festive table set with roses" style="background:linear-gradient(135deg,#2a1a14,#8a3a2a 50%,#1e1410)"></div><h3>JONAS KRELL KONCERT</h3><p>Lorem Ipsum is simply dummy text of the printing...</p><div class="meta">Posted on 20 Feb 2014<span class="stars">★★★<b>★★</b></span></div><div class="pill" style="left:0;width:51px">Event</div><div class="pill" style="left:57px;width:82px">Till mine favorite</div></article>
    <article class="abs card" style="left:447px;top:934px"><div class="photo" role="img" aria-label="Photo of a cheering concert audience" style="background:linear-gradient(180deg,#e8d8c8,#a06a48 45%,#2a1a14)"></div><h3>JONAS KRELL KONCERT</h3><p>Lorem Ipsum is simply dummy text of the printing...</p><div class="meta">Posted on 20 Feb 2014<span class="stars">★★★<b>★★</b></span></div><div class="pill" style="left:0;width:51px">Event</div><div class="pill" style="left:57px;width:82px">Till mine favorite</div></article>

    <!-- row 4 -->
    <article class="abs card" style="left:135px;top:1150px"><div class="photo" role="img" aria-label="Photo of a banquet hall with warm lighting" style="background:linear-gradient(160deg,#c06a20,#7a2a10 50%,#e0a050)"></div><h3>JONAS KRELL KONCERT</h3><p>Lorem Ipsum is simply dummy text of the printing...</p><div class="meta">Posted on 20 Feb 2014<span class="stars">★★★<b>★★</b></span></div><div class="pill" style="left:0;width:51px">Event</div><div class="pill" style="left:57px;width:82px">Till mine favorite</div></article>
    <article class="abs card" style="left:291px;top:1150px"><div class="photo" role="img" aria-label="Photo of a woman holding a glass of wine" style="background:linear-gradient(135deg,#1a120e,#6a3a22 50%,#d8b49a)"></div><h3>JONAS KRELL KONCERT</h3><p>Lorem Ipsum is simply dummy text of the printing...</p><div class="meta">Posted on 20 Feb 2014<span class="stars">★★★<b>★★</b></span></div><div class="pill" style="left:0;width:51px">Event</div><div class="pill" style="left:57px;width:82px">Till mine favorite</div></article>
    <article class="abs card" style="left:447px;top:1150px"><div class="photo" role="img" aria-label="Photo of shared dishes on a dinner table" style="background:linear-gradient(135deg,#e8dccc,#b07a48 50%,#6a3a1e)"></div><h3>JONAS KRELL KONCERT</h3><p>Lorem Ipsum is simply dummy text of the printing...</p><div class="meta">Posted on 20 Feb 2014<span class="stars">★★★<b>★★</b></span></div><div class="pill" style="left:0;width:51px">Event</div><div class="pill" style="left:57px;width:82px">Till mine favorite</div></article>

    <div class="abs pager">
      <span class="wide">Prev</span><span>1</span><span>2</span><span>3</span><span>4</span><span>5</span><span>6</span><span>...</span><span>22</span><span class="wide">Next</span>
    </div>
  </main>

  <aside>
    <div class="abs sidebar"></div>
    <div class="abs section-label" style="left:628px;top:468px">MINE FAVORITTER</div>
    <div class="abs fav" style="top:498px" role="img" aria-label="Photo of a couple at a concert"><div style="position:absolute;inset:0;background:linear-gradient(135deg,#5a1a4a,#b0506a 50%,#2a1030)"></div><div class="cap">JONAS KRELL KONCERT</div></div>
    <div class="abs fav" style="top:613px" role="img" aria-label="Photo of a woman with a cocktail at a party"><div style="position:absolute;inset:0;background:linear-gradient(135deg,#0a0e3a,#2a3aa0 50%,#c0b0c0)"></div><div class="cap">JONAS KRELL KONCERT</div></div>
    <div class="abs fav" style="top:728px" role="img" aria-label="Photo of a crowded event hall"><div style="position:absolute;inset:0;background:linear-gradient(180deg,#d8b070,#6a4020 50%,#1a120c)"></div><div class="cap">JONAS KRELL KONCERT</div></div>
    <div class="abs btn-dark sidebar-btn" style="top:842px">SEE MORE FAVORITE</div>
    <div class="abs section-label" style="left:628px;top:891px">NYHEDSBREV</div>
    <p class="abs news-text">Lorem Ipsum is simply dummy text of the printing and typesetting industry. Lorem Ipsum has been the industry's...</p>
    <div class="abs email">Email Address</div>
    <div class="abs btn-dark" style="left:629px;top:992px;width:75px;height:24px">TILMED</div>
  </aside>

  <footer>
    <div class="abs footer"></div>
    <div class="abs foot-links">
      <span style="width:48px">ALLE</span><span style="width:54px">MUSIK</span><span style="width:56px">SPORT</span><span style="width:60px">TEATER</span><span style="width:74px">UDSTILLING</span><span style="width:60px">FELDRE</span><span style="width:52px">BORN</span><span style="width:61px">MOTION</span><span>DIVERSE</span>
    </div>
    <div class="abs copy">COPYRIGHT © 2014. KULTIVA. ALL RIGHTS RESERVED.</div>
    <div class="abs social" style="left:695px"></div>
    <div class="abs social" style="left:725px"></div>
    <div class="abs social" style="left:756px"></div>
    <div class="abs social" style="left:786px"></div>
  </footer>

</div>
</body>
</html>
```